Probate (Legal) Wordpress Design with Coding for Online Company

I need a Wordpress design with coding, pictures, content to be provided by me, fully responsive, and development. This is for a 6-7 page design.

Pages Needed: Home/About/Probate/Process/FAQ/Contact Us/Blog.

The home page should be organized as followed:
-Steps in Probate: Gather; Implement; Close (each step will come with content)
-Flat-Fee Price & Savings: Content will go here with a button to contact us (phone number) or just the phone number.
-You Have Questions, We Have Answers: five questions with content. Only one question answer to show at a time when clicked on the question from the list.
-Get to Know Us: a brief description with content about what we do and who we are.

Main image slogan: Helping Californians deal with loss with DIGNITY & UNDERSTATING (you may use a better slogan if you wish).

The Contact page should not have a map since we are an online company. We service the entire state of California in every county and city.

The About page should be simple, direct, and easy on the eye. It should have a brief description of who we are and it should have no more than 6 reasons why the client should hire us.

About our online California company. We are not attorneys but legal document assistants who prepare legal documents for probate estate when someone dies with or without a will and assets need to be distributed. We have a flat-fee for Formal Probate of $999 and $699 for Informal Probate. We are an online company and offer our services to the entire state of California in every county. We do everything over the phone and email. The turn around time for us to prepare the initial legal paperwork for the client is within 3-5 business days. We can prepare, file, serve and manage a probate matter from petition to closing. We are not attorneys so our prices are very affordable compare to the attorney.

The company name for the website will be www.velmarhollow.com, The Velmar Hollow Group.

I do not have a logo yet. The colors of the website should be easy on the eye and calming. THE SITE SHOULD BE SIMPLE AND STRAIGHT TO THE POINT. EASY TO NAVIGATE.

The company phone number should be very visible and should stand out to the client. It should also be clickable and ready to dial for smartphone users.

I do not want a contact form on the homepage. THE MAIN THING IS FOR THE POTENTIAL CLIENT TO CALL OUR OFFICE TO SIGN UP.

I do like some images of family or people since we are dealing with people who just lost a loved one. Not all the images have to be of people.

The site should not look like we practice law or that people can mistake us for attorneys.

Target Market(s)

People who just lost a loved one who had property, assets, in California but died with or without a will or trust. This is for people looking to hire non-attorneys.

Coding

Coded - Design and coding required

Font styles to use
Serif

Colors

Designer to choose colors to be used in the design.

Requirements
Must have
• Refer to Project Description.
Nice to have
• The sample images provided is what I am attracted to for the homepage image.
Should not have

```html
<!DOCTYPE html>
<html lang="en">
<head>
<meta charset="utf-8">
<title>Velmar Hollow – Probate Document Assistance</title>
<link href="https://fonts.googleapis.com/css2?family=Poppins:wght@400;500;600;700&family=Open+Sans:ital,wght@0,400;0,600;1,400;1,600&display=swap" rel="stylesheet">
<style>
:root{
  --blue:#2f86c9;
  --blue-deep:#1f6fb3;
  --navy:#1a3c6b;
  --ink:#1c1c1c;
  --text:#555;
  --dark:#222426;
  --light:#f0f1f3;
  --white:#fff;
  --line:#d9dde2;
}
*{box-sizing:border-box;margin:0;padding:0}
html,body{width:1200px;height:3742px;overflow:hidden}
body{position:relative;background:var(--white);font-family:"Open Sans",Arial,sans-serif;color:var(--text)}
h1,h2,h3,h4,.nav,.btn,.brand{font-family:"Poppins",Arial,sans-serif}
section,header,footer{position:absolute;left:0;width:1200px}

/* hero */
.hero{top:0;height:640px;background:linear-gradient(100deg,#8c8a86 0%,#cfcac2 30%,#e9e4dc 50%,#a9a39b 75%,#6e6a66 100%)}
.hero-photo{position:absolute;inset:0}
.hero::after{content:"";position:absolute;inset:0;background:rgba(20,25,35,.28)}
.topbar{position:absolute;top:0;left:0;width:1200px;height:100px;z-index:2}
.brand{position:absolute;left:97px;top:26px;font-size:38px;font-weight:700;color:var(--white)}
.top-phone{position:absolute;right:97px;top:16px;color:var(--white);font-family:"Poppins",sans-serif;font-size:19px;font-weight:500;display:flex;align-items:center;gap:10px}
.nav{position:absolute;right:97px;top:54px;display:flex;gap:24px;font-size:17px;color:var(--white);font-weight:500}
.nav-rule{position:absolute;left:540px;right:97px;top:100px;border-top:1px solid rgba(255,255,255,.6)}
.hero-title{position:absolute;z-index:2;top:303px;left:0;width:1200px;text-align:center;color:var(--white);font-size:33px;font-weight:600;line-height:1.25;text-transform:uppercase}
.arrow{position:absolute;z-index:2;top:326px;width:34px;height:34px;border-radius:50%;background:rgba(0,0,0,.55);display:flex;align-items:center;justify-content:center}
.arrow.prev{left:66px}.arrow.next{right:66px}

/* about */
.about{top:537px;left:100px;width:1000px;height:288px;background:var(--blue);text-align:center;color:var(--white);z-index:3;padding:50px 80px 0}
.about h2{font-size:40px;font-weight:600;margin-bottom:18px}
.about p{font-size:12.5px;line-height:1.95}
.btn{display:inline-block;background:var(--navy);color:var(--white);font-size:14px;font-weight:600;padding:10px 22px;border-radius:3px;text-transform:uppercase;letter-spacing:.3px}
.about .btn{margin-top:18px}

/* steps */
.steps{top:825px;height:565px}
.steps-photo{position:absolute;left:75px;top:60px;width:515px;height:505px;background:radial-gradient(ellipse at 50% 55%,#d9e3ef 0%,#f4f6f9 60%,#fff 100%)}
.steps h2{position:absolute;left:640px;top:70px;font-size:33px;font-weight:500;color:var(--ink)}
.step{position:absolute;left:640px;width:480px;display:flex;gap:22px}
.step-icon{flex:none;width:86px;height:86px;border-radius:50%;background:var(--blue-deep);display:flex;align-items:center;justify-content:center;box-shadow:inset 0 0 0 5px var(--blue-deep),inset 0 0 0 8px var(--white)}
.step h3{font-size:20px;font-weight:500;color:var(--ink);margin:-2px 0 8px}
.step p{font-size:12.5px;line-height:1.75}

/* pricing band */
.pricing{top:1390px;height:470px;background:linear-gradient(110deg,#1d1f22 0%,#3a3c40 45%,#2a2c2f 100%);text-align:center;color:var(--white)}
.pricing-photo{position:absolute;inset:0}
.pricing::after{content:"";position:absolute;inset:0;background:rgba(0,0,0,.35)}
.pricing .inner{position:relative;z-index:1;padding:120px 190px 0}
.pricing h2{font-size:40px;font-weight:500;margin-bottom:16px}
.pricing p{font-size:13px;line-height:1.9}
.pricing .cta{margin-top:26px;display:flex;justify-content:center;align-items:center;gap:26px}
.pricing .btn{background:var(--blue);padding:9px 20px}
.cta-phone{display:flex;align-items:center;gap:10px;font-family:"Poppins",sans-serif;font-size:20px;font-weight:500}

/* know us */
.know{top:1860px;height:598px}
.know h2{position:absolute;top:58px;width:1200px;text-align:center;font-size:32px;font-weight:600;color:var(--ink)}
.know-card{position:absolute;top:150px;width:476px}
.know-card.left{left:110px}.know-card.right{left:636px}
.know-photo{height:230px;border:6px solid #eceef1}
.know-card.left .know-photo{background:linear-gradient(120deg,#b3875a 0%,#5e4a3a 40%,#2d2f3a 70%,#8e7e70 100%)}
.know-card.right .know-photo{background:linear-gradient(120deg,#d9dde3 0%,#9aa2ad 40%,#3a3f48 70%,#c6ccd4 100%)}
.know-card h3{font-size:24px;font-weight:600;color:var(--ink);margin:24px 0 10px}
.know-card p{font-size:12.5px;line-height:1.8}

/* faq */
.faq{top:2458px;height:524px;background:linear-gradient(135deg,#ececee 0%,#f6f6f7 50%,#eaeaec 100%)}
.faq h2{position:absolute;top:45px;width:1200px;text-align:center;font-size:32px;font-weight:600;color:var(--ink)}
.faq-list{position:absolute;left:250px;top:125px;width:700px}
.faq-q{height:36px;background:var(--white);border:1px solid var(--line);display:flex;align-items:center;justify-content:space-between;padding-left:16px;font-size:13px;color:#444;margin-bottom:6px}
.faq-q.open{background:#e5eef8;margin-bottom:0}
.faq-q .toggle{width:36px;height:36px;background:var(--blue-deep);display:flex;align-items:center;justify-content:center;margin-right:-1px}
.faq-a{background:#e5eef8;border:1px solid var(--line);border-top:0;padding:18px 16px;font-size:12.5px;line-height:1.75;color:#444;margin-bottom:34px}

/* testimonials */
.clients{top:2982px;height:418px;background:linear-gradient(90deg,#2a7fc6 0%,#3b8fd0 50%,#2a7fc6 100%);text-align:center;color:var(--white)}
.clients-photo{position:absolute;inset:0;opacity:.5}
.clients .inner{position:relative;z-index:1}
.clients h2{padding-top:58px;font-size:32px;font-weight:600}
.quote-mark{margin:28px auto 0;display:block}
.clients blockquote{margin:18px auto 0;width:820px;font-style:italic;font-size:13px;line-height:1.85}
.clients cite{display:block;margin-top:18px;font-style:italic;font-weight:600;font-size:14px}
.dots{margin:16px auto 0;display:flex;justify-content:center;gap:6px}
.dots span{width:22px;height:3px;background:rgba(255,255,255,.5)}
.dots span.on{background:var(--white)}
.corner{position:absolute;width:58px;height:58px;border:3px solid var(--white)}
.corner.tl{left:195px;top:165px;border-right:0;border-bottom:0}
.corner.br{left:948px;top:330px;border-left:0;border-top:0}

/* footer */
.site-footer{top:3400px;height:290px;background:#f4f5f6}
.site-footer h4{font-size:16px;font-weight:600;color:var(--ink);letter-spacing:.5px;text-transform:uppercase;margin-bottom:22px}
.fcol{position:absolute;top:60px;font-size:13px;color:#444}
.fcol.contact{left:98px;width:240px}
.fcol.links{left:423px}
.fcol.news{left:615px;width:300px}
.contact li{list-style:none;display:flex;gap:10px;margin-bottom:16px;line-height:1.6}
.contact svg{flex:none;margin-top:4px}
.links li{list-style:none;margin-bottom:3px;line-height:1.45}
.links li::before{content:"›";margin-right:10px;color:#666}
.news p{font-size:12px;line-height:1.7;margin:-4px 0 14px}
.signup{display:flex;width:282px;height:38px}
.signup span{flex:1;border:1px solid var(--line);background:var(--white);font-size:11px;padding:11px 10px;color:#666}
.signup b{background:var(--blue-deep);color:var(--white);font-size:11px;font-weight:600;padding:11px 10px;text-transform:uppercase}
.socials{position:absolute;left:983px;top:124px;display:flex;gap:7px}
.socials span{width:22px;height:22px;border-radius:50%;background:#8c8f93}
.bottom-bar{top:3690px;height:52px;background:#eceef0;text-align:center;font-size:12px;line-height:52px;color:#555}
</style>
</head>
<body>

<header class="hero">
  <div class="hero-photo" role="img" aria-label="Photo of a smiling advisor meeting clients at an office table"></div>
  <div class="topbar">
    <div class="brand">Velmar Hollow</div>
    <div class="top-phone">
      <svg width="18" height="18" viewBox="0 0 24 24" fill="#fff"><path d="M6.6 10.8a15.1 15.1 0 0 0 6.6 6.6l2.2-2.2c.3-.3.7-.4 1-.2 1.1.4 2.3.6 3.6.6.6 0 1 .4 1 1V20c0 .6-.4 1-1 1A17 17 0 0 1 3 4c0-.6.4-1 1-1h3.5c.6 0 1 .4 1 1 0 1.3.2 2.5.6 3.6.1.3 0 .7-.2 1z"/></svg>
      Call Us: 555-014-2277
    </div>
    <nav class="nav"><span>Home</span><span>About</span><span>Probate</span><span>Process</span><span>FAQ</span><span>Contact Us</span><span>Blog</span></nav>
    <div class="nav-rule"></div>
  </div>
  <a class="arrow prev"><svg width="12" height="12" viewBox="0 0 12 12"><path d="M8 1 3 6l5 5" stroke="#fff" stroke-width="2" fill="none"/></svg></a>
  <h1 class="hero-title">Helping Californians deal<br>with loss with dignity<br>&amp; understating</h1>
  <a class="arrow next"><svg width="12" height="12" viewBox="0 0 12 12"><path d="m4 1 5 5-5 5" stroke="#fff" stroke-width="2" fill="none"/></svg></a>
</header>

<section class="about">
  <h2>About Velmar Hollow</h2>
  <p>About our online California company. We are not attorneys but legal document assistants who prepare legal documents for probate estate when someone dies with or without a will and assets need to be distributed. We have a flat fee for Formal Probate of $999 and $699 for Informal Probate. We are an online company and offer our services to the entire state of California in every county.</p>
  <a class="btn">Read More</a>
</section>

<section class="steps">
  <div class="steps-photo" role="img" aria-label="Photo of a smiling man in glasses holding a laptop"></div>
  <h2>Steps in Probate</h2>
  <div class="step" style="top:148px">
    <div class="step-icon"><svg width="40" height="40" viewBox="0 0 40 40" fill="none" stroke="#fff" stroke-width="2.2"><circle cx="13" cy="12" r="5"/><circle cx="27" cy="12" r="5"/><path d="M5 30c0-5 4-9 8-9s8 4 8 9M19 30c0-5 4-9 8-9s8 4 8 9"/></svg></div>
    <div><h3>Gather</h3><p>Sed ut perspiciatis unde omnis iste natus error sit voluptatem accusantium doloremque laudantium, totam rem aperiam, eaque ipsa quae ab illo inventore</p></div>
  </div>
  <div class="step" style="top:285px">
    <div class="step-icon"><svg width="40" height="40" viewBox="0 0 40 40" fill="none" stroke="#fff" stroke-width="2.2"><circle cx="20" cy="20" r="6"/><circle cx="20" cy="20" r="13" stroke-dasharray="5 4"/></svg></div>
    <div><h3>Implement</h3><p>Sed ut perspiciatis unde omnis iste natus error sit voluptatem accusantium doloremque laudantium, totam rem aperiam, eaque ipsa quae ab illo inventore</p></div>
  </div>
  <div class="step" style="top:415px">
    <div class="step-icon"><svg width="40" height="40" viewBox="0 0 40 40" fill="none" stroke="#fff" stroke-width="2.2"><rect x="10" y="6" width="20" height="28" rx="2"/><path d="M14 13h12M14 18h12M14 23h7"/><path d="m21 28 3 3 6-6"/></svg></div>
    <div><h3>Close</h3><p>Sed ut perspiciatis unde omnis iste natus error sit voluptatem accusantium doloremque laudantium, totam rem aperiam, eaque ipsa quae ab illo inventore</p></div>
  </div>
</section>

<section class="pricing">
  <div class="pricing-photo" role="img" aria-label="Dark photo of hands signing documents on a desk"></div>
  <div class="inner">
    <h2>Flat Fee Price &amp; Savings</h2>
    <p>Sed ut perspiciatis unde omnis iste natus error sit voluptatem accusantium doloremque laudantium, totam rem aperiam, eaque ipsa quae ab illo inventore veritatis et quasi architecto beatae vitae dicta sunt explicabo. Nemo enim ipsam voluptatem quia voluptas sit aspernatur aut odit aut fugit, sed quia consequuntur magni dolores eos</p>
    <div class="cta">
      <a class="btn">Contact Us</a>
      <span class="cta-phone"><svg width="20" height="20" viewBox="0 0 24 24" fill="#fff"><path d="M6.6 10.8a15.1 15.1 0 0 0 6.6 6.6l2.2-2.2c.3-.3.7-.4 1-.2 1.1.4 2.3.6 3.6.6.6 0 1 .4 1 1V20c0 .6-.4 1-1 1A17 17 0 0 1 3 4c0-.6.4-1 1-1h3.5c.6 0 1 .4 1 1 0 1.3.2 2.5.6 3.6.1.3 0 .7-.2 1z"/></svg>Call Us: 555-014-2277</span>
    </div>
  </div>
</section>

<section class="know">
  <h2>GET TO KNOW US</h2>
  <div class="know-card left">
    <div class="know-photo" role="img" aria-label="Photo of three colleagues reviewing a folder together"></div>
    <h3>WHAT WE DO</h3>
    <p>Sed ut perspiciatis unde omnis iste natus error sit voluptatem accusantium doloremque laudantium, totam rem aperiam, eaque ipsa quae ab illo inventore veritatis et quasi architecto beatae vitae dicta sunt explicabo.</p>
  </div>
  <div class="know-card right">
    <div class="know-photo" role="img" aria-label="Photo of people reviewing paperwork at a meeting table"></div>
    <h3>WHO WE ARE</h3>
    <p>Sed ut perspiciatis unde omnis iste natus error sit voluptatem accusantium doloremque laudantium, totam rem aperiam, eaque ipsa quae ab illo inventore veritatis et quasi architecto beatae vitae dicta sunt explicabo.</p>
  </div>
</section>

<section class="faq">
  <h2>PROBATE FAQ</h2>
  <div class="faq-list">
    <div class="faq-q open">Where does it come from?<span class="toggle"><svg width="14" height="14" viewBox="0 0 14 14"><circle cx="7" cy="7" r="7" fill="#fff"/><path d="m4 6 3 3 3-3" stroke="#1f6fb3" stroke-width="1.6" fill="none"/></svg></span></div>
    <div class="faq-a">Lorem ipsum dolor sit amet, consectetur adipiscing elit, sed do eiusmod tempor incididunt ut labore et dolore magna aliqua. Ut enim ad minim veniam, quis nostrud exercitation ullamco laboris nisi ut aliquip ex ea commodo consequat. Duis aute irure dolor</div>
    <div class="faq-q">What is Lorem Ipsum?<span class="toggle"><svg width="14" height="14" viewBox="0 0 14 14"><circle cx="7" cy="7" r="7" fill="#fff"/><path d="m6 4 3 3-3 3" stroke="#1f6fb3" stroke-width="1.6" fill="none"/></svg></span></div>
    <div class="faq-q">Why do we use it?<span class="toggle"><svg width="14" height="14" viewBox="0 0 14 14"><circle cx="7" cy="7" r="7" fill="#fff"/><path d="m6 4 3 3-3 3" stroke="#1f6fb3" stroke-width="1.6" fill="none"/></svg></span></div>
    <div class="faq-q">Where does it come from?<span class="toggle"><svg width="14" height="14" viewBox="0 0 14 14"><circle cx="7" cy="7" r="7" fill="#fff"/><path d="m6 4 3 3-3 3" stroke="#1f6fb3" stroke-width="1.6" fill="none"/></svg></span></div>
    <div class="faq-q">Where can I get some?<span class="toggle"><svg width="14" height="14" viewBox="0 0 14 14"><circle cx="7" cy="7" r="7" fill="#fff"/><path d="m6 4 3 3-3 3" stroke="#1f6fb3" stroke-width="1.6" fill="none"/></svg></span></div>
  </div>
</section>

<section class="clients">
  <div class="clients-photo" role="img" aria-label="Faint blue-tinted photo of smiling clients"></div>
  <span class="corner tl"></span><span class="corner br"></span>
  <div class="inner">
    <h2>WHAT OUR CLIENTS SAY</h2>
    <svg class="quote-mark" width="56" height="44" viewBox="0 0 56 44" fill="#fff"><path d="M4 44V26C4 12 10 4 22 0l2 5c-7 3-10 8-10 15h10v24zM34 44V26c0-14 6-22 18-26l2 5c-7 3-10 8-10 15h10v24z"/></svg>
    <blockquote>" Sed ut perspiciatis unde omnis iste natus error sit voluptatem accusantium doloremque laudantium, totam rem aperiam, eaque ipsa quae ab illo inventore veritatis et quasi architecto beatae vitae dicta sunt explicabo. Nemo enim ipsam voluptatem quia voluptas sit aspernatur aut odit aut fugit, sed quia consequuntur .</blockquote>
    <cite>Alan Merrow - Velmar Hollow</cite>
    <div class="dots"><span class="on"></span><span></span></div>
  </div>
</section>

<footer class="site-footer">
  <div class="fcol contact">
    <h4>Contacts Us</h4>
    <ul>
      <li><svg width="11" height="14" viewBox="0 0 12 16" fill="#2f86c9"><path d="M6 0a6 6 0 0 0-6 6c0 4.5 6 10 6 10s6-5.5 6-10a6 6 0 0 0-6-6zm0 8.3A2.3 2.3 0 1 1 6 3.7a2.3 2.3 0 0 1 0 4.6z"/></svg><span>Velmar Hollow, 100, 22 Linden Row, California</span></li>
      <li><svg width="13" height="13" viewBox="0 0 24 24" fill="#2f86c9"><path d="M6.6 10.8a15.1 15.1 0 0 0 6.6 6.6l2.2-2.2c.3-.3.7-.4 1-.2 1.1.4 2.3.6 3.6.6.6 0 1 .4 1 1V20c0 .6-.4 1-1 1A17 17 0 0 1 3 4c0-.6.4-1 1-1h3.5c.6 0 1 .4 1 1 0 1.3.2 2.5.6 3.6.1.3 0 .7-.2 1z"/></svg><span>Phone: (555) 013-4410</span></li>
      <li><svg width="13" height="11" viewBox="0 0 16 12" fill="#2f86c9"><path d="M0 0h16v12H0z"/><path d="m0 0 8 6 8-6" stroke="#f4f5f6" stroke-width="1.4" fill="none"/></svg><span>Email: info@velmarhollow.com</span></li>
    </ul>
  </div>
  <div class="fcol links">
    <h4>Quick Links</h4>
    <ul><li>Home</li><li>About</li><li>Probate</li><li>Process</li><li>FAQ</li><li>Contact Us</li><li>Blog</li></ul>
  </div>
  <div class="fcol news">
    <h4>Sign Up For Newsletter</h4>
    <p>Sed ut perspiciatis unde omnis iste natus error sit voluptatem accusantium doloremque laudantium</p>
    <div class="signup"><span>Enter Name</span><b>Subscribe</b></div>
  </div>
  <div class="socials"><span></span><span></span><span></span><span></span></div>
</footer>

<footer class="bottom-bar">©2017 Velmar Hollow , All Rights Reserved.</footer>

</body>
</html>
```